Visualisation Software brochure

i need a sales brochure for a new visualisation software company called Lumora Studio Max.
The software has been specifically designed for manufacturers, distributers and retailers in the design / décor / furnishing / building industries. It allows customers can then import unlimited numbers of digital photos of rooms from their own home or take advantage of a library of pre-made photos, and then render different products from your catalogue into that photo to see what the finished look will be.
i have attached:
1) a mock up of the home page of the website
2) example of brochure wording that i have put together (although i am a little unsure about what other words i can add - so any suggestions here would be good)
3) i have attached some examples of other brochures that i like and would like similar designs
I am after a classy brochure used by a large corporate technology company that is given to executives and gives an impression of quality, trustworthiness and innovation.
• the colour blue as per the colours on my website mock up provided in the design brief
• I like simple, smart, clean and uncluttered design
• I like simple, clean and uncluttered design
• I like pictures that fit in with my technology (whether that be home and interior design, mixing virtual world and real world, visualising an idea) rather than basic stock of corporate people
Updates
Target Market(s)
marketing professionals
Industry/Entity Type
Software
Font styles to use
Look and feel
Each slider illustrates characteristics of the customer's brand and the style your logo design should communicate.

```html
<!DOCTYPE html>
<html lang="en">
<head>
<meta charset="utf-8">
<title>Lumora Studio Max – Benefits</title>
<link href="https://fonts.googleapis.com/css2?family=Source+Sans+3:wght@300;700&display=swap" rel="stylesheet">
<style>
  :root {
    --page-white: #ffffff;
    --panel-grey: #5b5a5b;
    --panel-text: #f2f2f2;
    --photo-cream: #ece7df;
    --photo-warm: #d9cfc2;
    --photo-skin: #e6c9b6;
    --photo-denim: #2b4a78;
    --photo-denim-deep: #1f3a63;
  }
  * { margin: 0; padding: 0; box-sizing: border-box; }
  html, body {
    width: 927px;
    height: 1200px;
    overflow: hidden;
    background: var(--page-white);
  }
  .page {
    position: relative;
    width: 927px;
    height: 1200px;
    background: var(--page-white);
    font-family: "Source Sans 3", "Source Sans Pro", sans-serif;
  }
  .hero-photo {
    position: absolute;
    left: 0;
    top: 0;
    width: 463px;
    height: 1200px;
    background: linear-gradient(180deg,
      var(--photo-cream) 0%,
      var(--photo-cream) 15%,
      var(--photo-warm) 35%,
      var(--photo-cream) 50%,
      var(--photo-skin) 62%,
      var(--photo-cream) 72%,
      var(--photo-denim) 80%,
      var(--photo-denim-deep) 100%);
  }
  .benefits-panel {
    position: absolute;
    left: 490px;
    top: 0;
    width: 437px;
    height: 1200px;
    background: var(--panel-grey);
    color: var(--panel-text);
  }
  .benefit-group {
    position: absolute;
    left: 50px;
    width: 345px;
  }
  .benefit-group.retailer { top: 167px; }
  .benefit-group.consumer { top: 699px; }
  .benefit-heading {
    font-weight: 700;
    font-size: 15px;
    line-height: 18.4px;
    color: var(--page-white);
  }
  .benefit-list {
    list-style: none;
    font-weight: 300;
    font-size: 15px;
    line-height: 18.4px;
  }
  .benefit-list li {
    padding-left: 11px;
    text-indent: -11px;
  }
  .benefit-list li::before {
    content: "•";
    display: inline-block;
    width: 11px;
    text-indent: 0;
  }
</style>
</head>
<body>
<div class="page">
  <div class="hero-photo" role="img" aria-label="Woman relaxing on a sofa in jeans, tapping the keyboard of a laptop in a bright living room"></div>

  <section class="benefits-panel">
    <div class="benefit-group retailer">
      <h2 class="benefit-heading">Retailer Benefits:</h2>
      <ul class="benefit-list">
        <li>Be the market innovator and leader by combining technology and a dynamic, seamless, integrated and consistent level of customer service across all online, bricks-and-mortar and mobile channels that delivers the big wow factor</li>
        <li>Extend your reach - don't limit your technology footprint by only using Orchard apps - our solution leverages and optimises all mobile devices and desktops (OrchardOS, Droidra, Web). This equates to a larger watershed of customers and more sales</li>
        <li>Increase brand engagement as our bespoke and scalable visualisation application will help customers build a relationship with your company, brand, and products and then share that experience within their social circles</li>
        <li>Understand buyer behaviour by receiving real usage statistics to obtain valuable insight about your customers and conduct trend analysis to determine how your future strategies can further enhance your bottom-line</li>
        <li>Increased sales to further grow your business</li>
        <li>Maximise the exposure of your products by uploading your entire product catalogue into a visualisation software that makes them look real</li>
      </ul>
    </div>

    <div class="benefit-group consumer">
      <h2 class="benefit-heading">Consumer Benefits:</h2>
      <ul class="benefit-list">
        <li>Reduce your customer's purchase anxiety as they will have the knowledge that the products they are choosing from your range are the right choice</li>
        <li>Greater flexibility in the way they shop by being open 24/7 and being able to engage with your brand when they want and how they want. Happier customers and hence more sales.</li>
        <li>An easy-to-use interface along with guided help and tutorials for those less confident with technology</li>
        <li>Being able to make informed purchasing decisions as they can easily compare a large range of your products at the touch of a computer key</li>
        <li>Improved personalised buying experience by enabling customers to use photos of their own personal spaces and incorporate your products</li>
      </ul>
    </div>
  </section>
</div>
</body>
</html>
```